Web design

We need the design for the logo and website for a women fashion website. No coding required. The colors used should be neutral (maybe with a light touch of color), the style should be modern, slightly luxurious, not too crowded. The target market is young professionals who love trendy clothes.
Updates

Need extra days to review

Target Market(s)

Young professionals

Industry/Entity Type

Apparel

Number of Pages Required

5+ page

Font styles to use
Sans Serif
Other font styles liked:
• Montserrat, Engravers Gothic, Benton Sans, gotham-book

Colors

Designer to choose colors to be used in the design.

```html
<!DOCTYPE html>
<html lang="en">
<head>
<meta charset="utf-8">
<title>ORVELLE – Shipping Details</title>
<link href="https://fonts.googleapis.com/css2?family=Montserrat:wght@400;500;600&display=swap" rel="stylesheet">
<style>
:root{
  --gold:#d4a10a;
  --ink:#1b1b1f;
  --muted:#555;
  --grey:#d9d9d9;
  --line:#bdbdbd;
  --sale:#f0352b;
  --blush:#fbe4dd;
  --footer:#f4f2f0;
  --req:#e53935;
}
*{box-sizing:border-box;margin:0;padding:0}
html,body{width:958px;height:1200px;overflow:hidden;background:#fff}
body{font-family:"Montserrat",sans-serif;color:var(--ink);position:relative}
.abs{position:absolute}
.header{position:absolute;left:0;top:0;width:958px;height:60px;border-bottom:1px solid #e6e6e6}
.nav a{position:absolute;top:23px;font-size:11px;color:var(--ink);text-decoration:none;white-space:nowrap}
.nav .sale{color:var(--sale)}
.brand{position:absolute;font-weight:500;color:var(--ink);letter-spacing:1px;white-space:nowrap}
.tools{position:absolute;top:19px;left:735px;display:flex;align-items:center;gap:12px;font-size:9px}
.step-circle{position:absolute;width:32px;height:32px;border-radius:50%;color:#fff;font-size:17px;font-weight:500;display:flex;align-items:center;justify-content:center;background:var(--gold)}
.step-circle.off{background:var(--grey)}
.step-label{position:absolute;top:146px;font-size:11px;font-weight:500;transform:translateX(-50%);white-space:nowrap}
.step-label.off{color:#b8b8b8}
.section-title{position:absolute;font-size:12px;font-weight:600;letter-spacing:.2px}
.field{position:absolute;left:111px;width:363px;height:35px;border:1px solid var(--line);font-size:9.5px;color:var(--muted);padding:0 10px;display:flex;align-items:center;letter-spacing:.3px}
.field sup{color:var(--req);font-size:8px;margin-left:1px;position:relative;top:-2px}
.link{position:absolute;top:740px;font-size:10.5px;color:var(--gold);text-decoration:underline;text-underline-offset:2px}
.sub-title{position:absolute;left:111px;font-size:9.5px;font-weight:500}
.radio{position:absolute;left:111px;font-size:6.8px;display:flex;align-items:center;gap:4px;letter-spacing:.1px}
.radio i{width:7px;height:7px;border:1px solid #999;border-radius:50%;display:inline-block}
.order{position:absolute;left:534px;top:226px;width:307px;height:384px;border:1px solid #ddd}
.order .photo{position:absolute;left:12px;top:35px;width:112px;height:141px;background:linear-gradient(160deg,#e4e1dc,#c9b8a8 55%,#b3a091)}
.prod{position:absolute;left:145px;top:36px;font-size:7px;line-height:1}
.prod h3{font-size:10px;font-weight:500;letter-spacing:.5px;margin-bottom:6px}
.prod p{margin-bottom:9px}
.promo-input{position:absolute;left:10px;top:224px;width:214px;height:26px;border:1px solid #ccc;font-size:8px;padding:0 7px;display:flex;align-items:center;color:#333}
.apply{position:absolute;left:224px;top:224px;width:70px;height:26px;background:var(--ink);color:#fff;font-size:8px;font-weight:600;display:flex;align-items:center;justify-content:center}
.rule{position:absolute;left:10px;width:284px;height:1px;background:#ddd}
.total{position:absolute;left:12px;top:284px;width:282px;display:flex;justify-content:space-between;font-size:10px;font-weight:600}
.cta{position:absolute;left:11px;top:328px;width:284px;height:41px;background:var(--blush);font-size:12px;font-weight:500;display:flex;align-items:center;justify-content:center}
.footer{position:absolute;left:0;top:929px;width:958px;height:271px;background:var(--footer)}
.col h4{position:absolute;font-size:12px;font-weight:500;letter-spacing:.6px}
.col a{position:absolute;font-size:10.5px;color:#333;text-decoration:none;white-space:nowrap}
.social{position:absolute;top:141px;width:26px;height:26px;border:1px solid #333;border-radius:50%}
.legal{position:absolute;left:0;width:958px;top:234px;text-align:center;font-size:10.5px;color:#333}
</style>
</head>
<body>
<header class="header">
  <nav class="nav">
    <a style="left:80px">Latest Arrivals</a>
    <a style="left:173px">Clothes ⌄</a>
    <a style="left:246px">ORVELLE Club</a>
    <a class="sale" style="left:336px">On Sale</a>
  </nav>
  <div class="brand" style="left:432px;top:17px;font-size:20px">ORVELLE</div>
  <div class="tools">
    <svg width="14" height="14" viewBox="0 0 14 14" fill="none" stroke="#222" stroke-width="1.3"><circle cx="6" cy="6" r="4.5"/><path d="M9.5 9.5 13 13"/></svg>
    <span style="margin-left:12px">ENG ⌄</span>
    <svg width="18" height="16" viewBox="0 0 18 16" fill="none" stroke="#222" stroke-width="1.3"><path d="M9 15S1 10 1 5a4 4 0 0 1 8-1 4 4 0 0 1 8 1c0 5-8 10-8 10z"/></svg>
    <svg width="16" height="18" viewBox="0 0 16 18" fill="none" stroke="#222" stroke-width="1.3"><circle cx="8" cy="5" r="4"/><path d="M1 18c0-5 3-7 7-7s7 2 7 7"/></svg>
    <svg width="20" height="20" viewBox="0 0 20 20" fill="none" stroke="#222" stroke-width="1.3"><path d="M2 7h13v11H2z"/><path d="M5 7V5a3.5 3.5 0 0 1 7 0v2"/><circle cx="16" cy="15" r="4" fill="#d4a10a" stroke="none"/><text x="16" y="17.5" font-size="6" fill="#fff" stroke="none" text-anchor="middle" font-family="Montserrat,sans-serif">0</text></svg>
  </div>
</header>

<svg class="abs" style="left:0;top:0" width="958" height="140">
  <line x1="165" y1="117" x2="573" y2="116" stroke="#d4a10a" stroke-width="1"/>
  <line x1="573" y1="116" x2="771" y2="116" stroke="#d9d9d9" stroke-width="1"/>
</svg>
<div class="step-circle" style="left:149px;top:100px">1</div>
<div class="step-circle" style="left:350px;top:100px">2</div>
<div class="step-circle off" style="left:557px;top:100px">3</div>
<div class="step-circle off" style="left:755px;top:100px">4</div>
<div class="step-label" style="left:165px">REVIEW</div>
<div class="step-label" style="left:366px">SHIPPING DETAILS</div>
<div class="step-label off" style="left:573px">PAYMENT</div>
<div class="step-label off" style="left:771px">CONFIRMATION</div>

<div class="section-title" style="left:111px;top:227px">DELIVERY ADDRESS</div>
<div class="abs" style="left:111px;top:251px;width:364px;height:1px;background:#ddd"></div>
<div class="abs" style="left:111px;top:251px;width:227px;height:1px;background:var(--gold)"></div>

<div class="field" style="top:275px">First name<sup>*</sup></div>
<div class="field" style="top:315px">Last name<sup>*</sup></div>
<div class="field" style="top:356px">- Select Country/region -</div>
<div class="field" style="top:396px">Staste/province<sup>*</sup></div>
<div class="field" style="top:436px">Zip/postal code<sup>*</sup></div>
<div class="field" style="top:476px">Address<sup>*</sup></div>
<div class="field" style="top:517px">Address, line 2<sup>*</sup></div>
<div class="field" style="top:557px">City<sup>*</sup></div>
<div class="field" style="top:597px">Bussiness name<sup>*</sup></div>
<div class="field" style="top:638px">Mobile phone<sup>*</sup></div>
<div class="field" style="top:678px">Email Address<sup>*</sup></div>

<div class="link" style="left:111px">⟵ Back To Cart</div>
<div class="link" style="left:305px">Already have an account?Log in</div>

<div class="sub-title" style="top:775px">BILLING ADDRESS</div>
<div class="radio" style="top:794px"><i></i>CLICK TO USE SHIPPING ADDRESS AS BILLING ADDRESS</div>
<div class="sub-title" style="top:823px">SUBSCRIBE TO NEWSLETTER</div>
<div class="radio" style="top:842px"><i></i>YOU AGREE TO OUR TERMS AND SERVICES TEXT BELOW.</div>

<aside class="order">
  <div class="section-title" style="left:10px;top:11px">YOUR ORDER</div>
  <div class="photo" role="img" aria-label="Product photo: model wearing a beige knit off-shoulder top and skirt"></div>
  <div class="prod">
    <h3>‘THE STANDARD’</h3>
    <p style="margin-bottom:16px">Sed ut perspiciatis unde omnis</p>
    <p>Size:&nbsp; L+ (Regular cup)</p>
    <p>Quantity: 1</p>
    <p>Price: USD $129.00</p>
  </div>
  <svg class="abs" style="left:288px;top:38px" width="8" height="8" viewBox="0 0 8 8" stroke="#222" stroke-width="1"><path d="M0 0l8 8M8 0 0 8"/></svg>
  <div class="section-title" style="left:10px;top:204px;font-size:10.5px;font-weight:600;letter-spacing:.5px">PROMOTIONAL CODE AND GIFT CARD</div>
  <div class="promo-input">ENTER CODE</div>
  <div class="apply">APPLY</div>
  <div class="rule" style="top:270px"></div>
  <div class="total"><span>TOTAL:</span><span>USD $129.00</span></div>
  <div class="rule" style="top:309px"></div>
  <div class="cta">CONTINUE TO PAYMENT</div>
</aside>

<footer class="footer">
  <div class="brand" style="left:80px;top:66px;font-size:34px">ORVELLE</div>
  <div class="col">
    <h4 style="left:355px;top:62px">HELP</h4>
    <a style="left:355px;top:95px">Terms &amp; Conditions</a>
    <a style="left:355px;top:116px">Privacy Policy</a>
    <a style="left:355px;top:138px">Returns/exchanges</a>
    <a style="left:355px;top:159px">Delivery Information</a>
    <a style="left:355px;top:180px">FAQ</a>
  </div>
  <div class="col">
    <h4 style="left:588px;top:62px">SHOP</h4>
    <a style="left:588px;top:95px">Tops</a>
    <a style="left:588px;top:116px">Bootoms</a>
    <a style="left:588px;top:138px">Intimates</a>
    <a style="left:588px;top:159px">Dresses</a>
    <a style="left:588px;top:180px">Swim</a>
  </div>
  <div class="col">
    <h4 style="left:768px;top:62px">CONTACT US</h4>
    <a style="left:769px;top:84px;display:flex;align-items:center;gap:5px"><svg width="12" height="9" viewBox="0 0 12 9" fill="none" stroke="#333"><rect x=".5" y=".5" width="11" height="8"/><path d="M.5.5 6 5l5.5-4.5"/></svg>info@orvelle.com</a>
    <h4 style="left:768px;top:117px">FOLLOW US</h4>
  </div>
  <span class="social" style="left:765px"></span>
  <span class="social" style="left:794px"></span>
  <span class="social" style="left:823px"></span>
  <span class="social" style="left:852px"></span>
  <div class="abs" style="left:89px;top:215px;width:780px;height:1px;background:#ccc"></div>
  <div class="legal">Terms &amp; Conditions, Privacy Policy and @2021 followed by orvelle.</div>
</footer>
</body>
</html>
```